Local fast-growing company in the service sector

We are looking for a modern business card design, which should also appear on our letterheads

Target Market(s)

Private and industrial sectors

Contact Information for Business Card

Vorname Name
Kellberger Str. 18
74385 Lindenhain
Tel.: 07146-839214-0
Name@agentur-kvtl.de

Colors
9d9d9d
919191
aaaaaa

Requirements
Must have
• The logo (file) in silver

```html
<!DOCTYPE html>
<html lang="de">
<head>
<meta charset="utf-8">
<title>KVTL Visitenkarte</title>
<link rel="stylesheet" href="https://fonts.googleapis.com/css2?family=Roboto:wght@400;500;700&display=swap">
<style>
  :root {
    --bg: #1e1e1e;
    --silver-light: #f6f6f6;
    --silver-mid: #dedede;
    --silver-dark: #bcbcbc;
    --grey-band: #aaaaaa;
    --grey-mark: #9d9d9d;
    --grey-text: #6e6e6e;
    --grey-icon: #919191;
    --white: #ffffff;
  }
  * { margin: 0; padding: 0; box-sizing: border-box; }
  html, body { width: 1200px; height: 900px; overflow: hidden; }
  body {
    background: var(--bg);
    font-family: "Roboto", Arial, sans-serif;
    display: flex;
    flex-direction: column;
    align-items: center;
    justify-content: center;
    gap: 60px;
  }
  .card {
    position: relative;
    width: 560px;
    height: 320px;
    border-radius: 22px;
    overflow: hidden;
    background: linear-gradient(160deg,
      var(--silver-mid) 0%, var(--silver-light) 18%, var(--silver-dark) 34%,
      var(--silver-light) 50%, var(--silver-mid) 66%, var(--silver-light) 82%, var(--silver-dark) 100%);
  }
  .brand {
    display: flex;
    align-items: center;
    gap: 14px;
    color: var(--grey-mark);
    font-weight: 700;
    letter-spacing: 2px;
    white-space: nowrap;
  }
  .brand-square { background: var(--grey-mark); display: block; flex: none; }
  .card-front .brand {
    position: absolute; left: 50%; top: 50%;
    transform: translate(-50%, -50%);
    font-size: 64px;
  }
  .card-front .brand-square { width: 54px; height: 54px; }
  .card-back .brand {
    position: absolute; right: 30px; top: 34px;
    font-size: 42px; gap: 10px;
  }
  .card-back .brand-square { width: 36px; height: 36px; }
  .name-band {
    position: absolute; left: 0; top: 128px;
    width: 300px; height: 76px;
    background: var(--grey-band);
    padding: 14px 0 0 34px;
    color: var(--white);
  }
  .person-name { font-size: 24px; font-weight: 500; letter-spacing: 0.5px; white-space: nowrap; }
  .person-role { font-size: 13px; letter-spacing: 1px; margin-top: 2px; }
  .address {
    position: absolute; right: 34px; top: 150px;
    text-align: right; font-size: 14px; line-height: 1.4;
    font-style: normal;
    color: var(--grey-text);
  }
  .contact-list {
    position: absolute; left: 34px; bottom: 24px;
    list-style: none; font-size: 14px; line-height: 1.45;
    color: var(--grey-text);
  }
  .contact-list li { display: flex; align-items: center; gap: 10px; }
  .contact-list svg { width: 12px; height: 12px; fill: var(--grey-icon); flex: none; }
</style>
</head>
<body>
  <section class="card card-front">
    <div class="brand"><span class="brand-square"></span>KVTL</div>
  </section>

  <section class="card card-back">
    <div class="brand"><span class="brand-square"></span>KVTL</div>
    <div class="name-band">
      <p class="person-name">MARTIN KELLER</p>
      <p class="person-role">DIRECTOR</p>
    </div>
    <address class="address">Kellberger Str. 18<br>74385 Lindenhain</address>
    <ul class="contact-list">
      <li><svg viewBox="0 0 12 12"><path d="M2 1h3l1 3-1.5 1a6 6 0 0 0 2.5 2.5L8 6l3 1v3a1 1 0 0 1-1 1A9 9 0 0 1 1 2a1 1 0 0 1 1-1z"/></svg>07146-839214-0</li>
      <li><svg viewBox="0 0 12 12"><path d="M3 0h6a1 1 0 0 1 1 1v10a1 1 0 0 1-1 1H3a1 1 0 0 1-1-1V1a1 1 0 0 1 1-1zm0 2v7h6V2z"/></svg>0162-48305917</li>
      <li><svg viewBox="0 0 12 12"><path d="M3 0h5v4H3zM1 5h10v7H1zm2 2v1h2V7zm4 0v1h2V7z"/></svg>07146-839214-9</li>
      <li><svg viewBox="0 0 12 12"><path d="M0 2h12v8H0zm1 1v.5l5 3.5 5-3.5V3z"/></svg>Name@agentur-kvtl.de</li>
    </ul>
  </section>
</body>
</html>
```